Web Page Design for a Website that Provides Tutoring

I am looking to create an online tutoring website. The website will allow parents or students to contact tutors with a view to instructing them to tutor themselves or their children.

The name of the website is LendYourLessons.

This brief is to create the design for one of the web pages for this web site. I am hoping the same designer will be available to design other pages.

The page I want designed is one of the more complex and I have attached the design as an excel spreadsheet. The web page needs to include all the items on this page but if you want to change the positioning of the items then Im fine with that.

I recently had two logos created for this website. My favourite is the one with a mortar board but im not sure I like the colours. I have attached both of these logos and you can use either of them, change the colours or create something different. I just want a design pleasing to the eye. If the logo is changed I would like that in a seperate file.

So can you please submit designs for this page. I have attached the two logos which you can use, change or if you feel you have a better idea then you can use that.

On the spreadsheet the Send Message, Favourite etc are buttons.

Target Market(s)

People who want to better themselves.
Possible middle class to upper class.

Industry/Entity Type

Tutoring

Number of Pages Required

1 page

Requirements
Must have
• The designs must have alot of the information attached in the spreadsheet.

```html
<!DOCTYPE html>
<html lang="en">
<head>
<meta charset="utf-8">
<title>LendYourLessons – Tutor Profile</title>
<link href="https://fonts.googleapis.com/css2?family=Roboto:wght@300;400;500;700&family=Raleway:wght@400;500&display=swap" rel="stylesheet">
<style>
:root{
  --orange:#f7931e;
  --coral:#ff6640;
  --navy:#2f4f8f;
  --ink:#333;
  --muted:#666;
  --line:#d6d6d6;
  --panel:#eef1fb;
  --band:#2a2d33;
  --footer:#3d62a8;
  --avail:#d9fbd3;
}
*{box-sizing:border-box;margin:0;padding:0}
html,body{width:898px;height:1200px;overflow:hidden}
body{position:relative;background:#fff;font-family:"Roboto",Arial,sans-serif;color:var(--ink);font-size:9px}
.abs{position:absolute}
/* header */
.site-header{position:absolute;left:0;top:0;width:898px;height:70px;background:#fff}
.brand{position:absolute;left:60px;top:22px;font-size:22px;font-weight:700;color:var(--orange);display:flex;align-items:center;gap:6px}
.brand-mark{width:12px;height:12px;background:var(--navy)}
.main-nav a{position:absolute;top:30px;font-size:11px;color:#333;text-decoration:none}
.main-nav a.active{color:var(--navy);border-bottom:1px solid var(--navy);padding-bottom:2px}
.btn{position:absolute;display:flex;align-items:center;justify-content:center;color:#fff;font-size:10px;font-weight:500;border-radius:2px}
.btn-login{left:692px;top:22px;width:68px;height:26px;background:var(--orange)}
.btn-register{left:768px;top:22px;width:69px;height:26px;background:var(--coral)}
.crumb-band{position:absolute;left:0;top:70px;width:898px;height:42px;background:var(--band)}
.crumb{position:absolute;left:60px;top:12px;font-size:13.5px;color:#c8c8c8;font-weight:300}
.btn-favour{left:768px;top:11px;width:66px;height:20px;border:1px solid var(--coral);color:var(--coral);font-size:8px;border-radius:1px}
/* cards */
.card{position:absolute;border:1px solid var(--line);background:#fff}
.card-head{height:26px;color:#fff;font-size:12px;font-weight:500;padding:7px 8px;background:var(--orange)}
.card-head.coral{background:var(--coral);padding-left:12px}
.star-row{display:flex;gap:2px}
.star-row svg{width:13px;height:13px}
.profile-photo{position:absolute;left:10px;top:11px;width:128px;height:137px;background:linear-gradient(160deg,#b9b6b0,#6b6a6a 60%,#3c3e44)}
.profile-main{position:absolute;left:158px;top:11px;width:150px}
.profile-main h1{font-size:16px;font-weight:400;color:#222}
.profile-main p{font-size:8.5px;color:var(--muted);line-height:1.4}
.lbl{font-weight:500;color:#222}
.profile-side{position:absolute;left:318px;top:0;width:193px;height:160px;background:var(--panel);padding:7px 14px;font-size:8.5px;color:var(--muted);line-height:17.3px}
.info-text{position:absolute;font-size:8.6px;line-height:12px;color:#444}
table.subjects{position:absolute;left:0;top:26px;width:510px;border-collapse:collapse;font-size:10px}
.subjects th{background:#d8d8d8;height:24px;font-weight:400;font-size:8.6px;color:#444;text-align:left}
.subjects td{height:23px;color:#333}
.subjects tr.first td{padding-top:6px;border-bottom:1px solid #ddd}
.day-head{position:absolute;left:0;top:26px;width:510px;height:24px;background:#d8d8d8}
.day-head span,.slot-lbl{position:absolute;font-size:8.6px;color:#444}
.grid-area{position:absolute;left:74px;top:60px;width:426px;height:69px;background:var(--avail)}
.bar{position:absolute;height:7px}
.legend{position:absolute;left:120px;top:146px;display:flex;gap:12px;font-size:8.6px;color:#666}
.legend i{display:inline-block;width:7px;height:7px;margin-right:5px}
/* contact */
.msg-box{position:absolute;left:15px;top:42px;width:220px;height:77px;border:1px solid #ccc;background:#fff;font-size:9.5px;color:#999;padding:10px 9px}
.check{position:absolute;font-size:10px;color:#444;display:flex;align-items:center;gap:8px}
.check i{width:13px;height:13px;border:1px solid #bbb;background:#fff;border-radius:2px}
.btn-submit{left:164px;top:170px;width:68px;height:24px;background:var(--navy);font-weight:700}
.review{position:absolute;left:14px;width:219px;height:137px;border:1px solid #ccc;background:var(--panel)}
.avatar{position:absolute;left:12px;top:12px;width:43px;height:42px}
.review .star-row{position:absolute;left:64px;top:37px}
.review p{position:absolute;left:14px;top:64px;width:192px;font-size:8.6px;line-height:12px;color:#333}
.review .who{top:115px;left:20px}
.btn-all{left:54px;top:340px;width:157px;height:23px;border:1px solid var(--coral);color:var(--coral);font-size:10px;font-weight:400}
/* footer */
.site-footer{position:absolute;left:0;top:876px;width:898px;height:286px;background:linear-gradient(135deg,#4a6db0,#3558a0 55%,#4769ad)}
.site-footer h3{position:absolute;font-family:"Raleway",sans-serif;font-weight:400;font-size:16px;color:var(--orange)}
.rule{position:absolute;height:1px;background:rgba(255,255,255,.35)}
.flink{position:absolute;font-size:10px;color:#fff}
.flink::before{content:"";display:inline-block;border-left:3px solid #fff;border-top:2.5px solid transparent;border-bottom:2.5px solid transparent;margin-right:6px;vertical-align:1px}
.ftxt{position:absolute;font-size:9px;color:#fff;line-height:12px}
.map{position:absolute;left:524px;top:84px;width:126px;height:95px;border:3px solid rgba(255,255,255,.4);background:linear-gradient(135deg,#e9e3cf,#d8d2bc 50%,#e6d67f)}
.social{position:absolute;left:698px;font-size:9.5px;color:#fff;display:flex;align-items:center;gap:9px}
.social i{width:18px;height:18px;background:rgba(255,255,255,.85);border-radius:2px}
.bottom-bar{position:absolute;left:0;top:1162px;width:898px;height:38px;background:var(--orange);color:#fff;font-size:8.3px}
</style>
</head>
<body>
<svg width="0" height="0" style="position:absolute">
  <defs>
    <symbol id="star" viewBox="0 0 24 24"><path d="M12 1.5l3.2 7.1 7.7.8-5.8 5.2 1.7 7.6L12 18.3l-6.8 3.9 1.7-7.6L1.1 9.4l7.7-.8z"/></symbol>
  </defs>
</svg>

<header class="site-header">
  <div class="brand"><span class="brand-mark"></span>LendYourLessons</div>
  <nav class="main-nav">
    <a style="left:358px">Home</a>
    <a class="active" style="left:411px">Search</a>
    <a style="left:468px">Student</a>
    <a style="left:531px">Tutor</a>
    <a style="left:585px">About</a>
    <a style="left:639px">Contact</a>
  </nav>
  <div class="btn btn-login">Login</div>
  <div class="btn btn-register">Register</div>
</header>

<div class="crumb-band">
  <div class="crumb">Home &gt; Search &gt; Teacher Name</div>
  <div class="btn btn-favour">FAVOUR</div>
</div>

<!-- profile -->
<section class="card" style="left:60px;top:136px;width:512px;height:162px">
  <div class="profile-photo" role="img" aria-label="Portrait photo of the tutor"></div>
  <div class="profile-main">
    <h1>Daniel Hart</h1>
    <p style="margin-top:4px">Bachelor Degree in History from the University of Castellmar</p>
    <p class="lbl" style="margin-top:9px">Knowledge Centre :</p>
    <div class="star-row" style="margin-top:3px;fill:var(--coral)">
      <svg><use href="#star"/></svg><svg><use href="#star"/></svg><svg><use href="#star"/></svg><svg><use href="#star"/></svg><svg style="fill:#bbb"><use href="#star"/></svg>
    </div>
    <p style="margin-top:6px"><span class="lbl">Tutoring Type :</span> Lorem Ipsum</p>
    <p style="margin-top:5px"><span class="lbl">Willing To Travel:</span> Lorem Ipsum</p>
  </div>
  <div class="profile-side">
    <div class="lbl">Feedback Score:</div>
    <div class="star-row" style="fill:var(--coral);margin:-1px 0 3px">
      <svg><use href="#star"/></svg><svg><use href="#star"/></svg><svg><use href="#star"/></svg><svg><use href="#star"/></svg><svg style="fill:#bbb"><use href="#star"/></svg>
    </div>
    <div><span class="lbl">Education:</span> Lorem Ipsum</div>
    <div><span class="lbl">Gender :</span> Male</div>
    <div><span class="lbl">Member Since&nbsp; :</span> 12th Jan 2014</div>
    <div><span class="lbl">Location :</span> California, USA</div>
    <div><span class="lbl">Response Rate:</span> 75%</div>
    <div><span class="lbl">Expected Response:</span> &lt; 20 hours</div>
  </div>
</section>

<!-- tutor information -->
<section class="card" style="left:60px;top:318px;width:512px;height:162px">
  <div class="card-head">Tutor Informtion</div>
  <div class="info-text" style="left:18px;top:40px;width:282px">Hello,<br><br>My name is Daniel Hart, and I am a Historian specialized in languages and Ancient History. I am from Barcelona but I studied in different places of Spain. I have a Bachelor Degree in History from the University of Castellmar. This degree is structured in a significant freedom of subjects choice (three years studying universal, general and heoretical History and two years studying Ancient History, Art, Languages and Beliefs). Besides, I started an Undergraduate</div>
  <div class="abs" style="left:320px;top:40px;width:1px;height:102px;background:#ddd"></div>
  <div class="info-text" style="left:334px;top:40px;width:160px"><b style="font-weight:500;color:#222">Qualification</b><br><br>Bachelor Degree in History from the University of Castellmar Undergraduate Degree in Classical Studies from Autonomous Ribera University</div>
  <div class="abs" style="left:506px;top:35px;width:2px;height:112px;background:#ddd"></div>
  <div class="abs" style="left:506px;top:35px;width:2px;height:16px;background:var(--coral)"></div>
</section>

<!-- subjects -->
<section class="card" style="left:60px;top:500px;width:512px;height:116px">
  <div class="card-head">Subjects Taught</div>
  <table class="subjects">
    <tr><th style="padding-left:10px;width:92px"></th><th style="width:55px">Primary</th><th style="width:57px">Secondary</th><th style="width:57px">GCSE</th><th style="width:65px">A-LEVEL</th><th style="width:75px">University</th><th>Adult Learner</th></tr>
    <tr class="first"><td style="padding-left:11px">Biology</td><td>£20</td><td>£20</td><td>£50</td><td></td><td>£20</td><td>£20</td></tr>
    <tr><td style="padding-left:11px">Chemistry</td><td>£20</td><td>£30</td><td>£20</td><td></td><td>£20</td><td>£20</td></tr>
  </table>
</section>

<!-- availability -->
<section class="card" style="left:60px;top:636px;width:512px;height:176px">
  <div class="card-head">Availability</div>
  <div class="abs" style="left:379px;top:8px;font-size:8.5px;color:#fff">Select Date</div>
  <svg class="abs" style="left:428px;top:4px" width="17" height="17" viewBox="0 0 17 17" fill="none" stroke="#fff" stroke-width="1.2"><rect x="1.5" y="3" width="14" height="12.5"/><path d="M1.5 6.5h14M5 1v3M12 1v3M4 9h2M8 9h2M12 9h1M4 12h2M8 12h2M12 12h1"/></svg>
  <svg class="abs" style="left:463px;top:7px" width="40" height="12" viewBox="0 0 40 12" fill="none" stroke="#fff" stroke-width="1.4"><path d="M6 1L1.5 6 6 11M33 1l4.5 5L33 11"/></svg>
  <div class="day-head">
    <span style="left:75px;top:7px">Mon Day</span><span style="left:139px;top:7px">Tues Day</span><span style="left:202px;top:7px">Wednes Day</span><span style="left:279px;top:7px">Thurs Day</span><span style="left:350px;top:7px">Fri Day</span><span style="left:403px;top:7px">Satur Day</span><span style="left:464px;top:7px">Sun Day</span>
  </div>
  <span class="slot-lbl" style="left:11px;top:64px">7-8PM</span>
  <span class="slot-lbl" style="left:11px;top:89px">8-9PM</span>
  <span class="slot-lbl" style="left:11px;top:115px">4-5PM</span>
  <div class="grid-area">
    <div class="bar" style="left:132px;top:12px;width:40px;background:var(--coral)"></div>
    <div class="bar" style="left:132px;top:28px;width:40px;background:var(--orange)"></div>
    <div class="bar" style="left:132px;top:48px;width:40px;background:var(--navy)"></div>
    <div class="bar" style="left:270px;top:48px;width:39px;background:var(--orange)"></div>
    <div class="bar" style="left:386px;top:22px;width:39px;background:var(--navy)"></div>
  </div>
  <div class="legend">
    <span><i style="background:var(--avail)"></i>Available</span>
    <span><i style="background:var(--coral)"></i>Taken</span>
    <span><i style="background:var(--orange)"></i>Reserved</span>
    <span><i style="background:var(--navy)"></i>No</span>
  </div>
</section>

<!-- contact -->
<aside class="card" style="left:592px;top:136px;width:246px;height:215px;background:var(--panel)">
  <div class="card-head coral">Contact Daniel Hart</div>
  <div class="msg-box">Enter your messages</div>
  <div class="check" style="left:13px;top:134px"><i></i>Teacher</div>
  <div class="check" style="left:78px;top:134px"><i></i>Full time tutor</div>
  <div class="check" style="left:13px;top:154px"><i></i>Full time student</div>
  <div class="btn btn-submit">SUBMIT</div>
</aside>

<!-- reviews -->
<aside class="card" style="left:592px;top:370px;width:246px;height:383px;background:var(--panel)">
  <div class="card-head coral">Tutors Review</div>
  <div class="review" style="top:41px">
    <div class="avatar" role="img" aria-label="Reviewer photo" style="background:linear-gradient(160deg,#d9cbb8,#7a5a44)"></div>
    <div class="star-row" style="fill:var(--coral)"><svg><use href="#star"/></svg><svg><use href="#star"/></svg><svg><use href="#star"/></svg><svg><use href="#star"/></svg><svg style="fill:#bbb"><use href="#star"/></svg></div>
    <p>“Lorem ipsum dolor sit amet, consectetur adipiscing elit. Donec et quam nunc. Nam tortor sapien, volutpat consectetur lacus ut, accumsan viverra urna. ”</p>
    <p class="who">- Student Name</p>
  </div>
  <div class="review" style="top:189px">
    <div class="avatar" role="img" aria-label="Reviewer photo" style="background:linear-gradient(160deg,#c9a67c,#8b5a3e)"></div>
    <div class="star-row" style="fill:var(--coral)"><svg><use href="#star"/></svg><svg><use href="#star"/></svg><svg><use href="#star"/></svg><svg style="fill:#bbb"><use href="#star"/></svg><svg style="fill:#bbb"><use href="#star"/></svg></div>
    <p>“Lorem ipsum dolor sit amet, consectetur adipiscing elit. Donec et quam nunc. Nam tortor sapien, volutpat consectetur lacus ut, accumsan viverra urna. ”</p>
    <p class="who">- Student Name</p>
  </div>
  <div class="btn btn-all">TO SEE ALL REVIEWS</div>
</aside>

<!-- footer -->
<footer class="site-footer" role="img" aria-label="Background photo of students studying at a desk">
  <h3 style="left:60px;top:50px">Quick Links</h3>
  <div class="rule" style="left:60px;top:73px;width:199px"></div>
  <div class="flink" style="left:62px;top:86px">Home</div>
  <div class="flink" style="left:62px;top:106px">About</div>
  <div class="flink" style="left:62px;top:126px">Search</div>
  <div class="flink" style="left:62px;top:146px">Student</div>
  <div class="flink" style="left:62px;top:166px">Tutor</div>
  <div class="flink" style="left:62px;top:186px">Contacts</div>
  <div class="flink" style="left:157px;top:86px">Privacy Policy</div>
  <div class="flink" style="left:157px;top:106px">User Agreement</div>

  <h3 style="left:298px;top:52px">Contact Information</h3>
  <div class="rule" style="left:298px;top:73px;width:212px"></div>
  <svg class="abs" style="left:298px;top:87px" width="8" height="11" viewBox="0 0 8 11"><path d="M4 0a4 4 0 0 0-4 4c0 3 4 7 4 7s4-4 4-7a4 4 0 0 0-4-4zm0 5.5A1.5 1.5 0 1 1 4 2.5a1.5 1.5 0 0 1 0 3z" fill="#fff"/></svg>
  <div class="ftxt" style="left:312px;top:87px;width:210px">ABN 51204773918&nbsp; Head Office, 8 Marlow Court Drive, Science Park, Kelvale 6120<br>PO Box 410 Kelvale DC 6120</div>
  <svg class="abs" style="left:298px;top:135px" width="6" height="11" viewBox="0 0 6 11"><path d="M5 1C2 2 1 4 1 5.5S2 9 5 10" stroke="#fff" stroke-width="2" fill="none"/></svg>
  <div class="ftxt" style="left:312px;top:132px;font-size:12px;color:var(--orange)">FREECALL 1800 555 014</div>
  <svg class="abs" style="left:296px;top:159px" width="10" height="7" viewBox="0 0 10 7"><rect width="10" height="7" fill="#fff"/><path d="M0 0l5 4 5-4" stroke="#3d62a8" fill="none"/></svg>
  <div class="ftxt" style="left:316px;top:157px">info@lendyourlessons.com</div>
  <div class="map" role="img" aria-label="Street map showing the head office location"></div>

  <h3 style="left:698px;top:50px">Follow Us</h3>
  <div class="rule" style="left:698px;top:73px;width:140px"></div>
  <div class="social" style="top:86px"><i></i>Friendbook</div>
  <div class="social" style="top:111px"><i></i>Linkfolio</div>
  <div class="social" style="top:136px"><i></i>Chirper</div>
  <div class="social" style="top:161px"><i></i>Email</div>
</footer>

<div class="bottom-bar">
  <span class="abs" style="left:56px;top:15px">Copyright@lendyourlessons.com. All Rights Are Reserved.</span>
  <span class="abs" style="left:652px;top:15px">Join Us&nbsp; -&nbsp; Login to lendyourlessons Online&nbsp; -&nbsp; Support</span>
</div>
</body>
</html>
```